Profesional personal website needs design and business card

I need a business card with my professional name as a logo "Dorian Vitality" for my business. I am a Wellness Coach, consultant and trainer. So it should be professional, wellness oriented and modern.

Target Market(s)

Private clients, governments, corporations. Luxury and high market.

Industry/Entity Type

Health And Wellness

Contact Information for Business Card

Dorian Vitality should be the logo

Colors

Designer to choose colors to be used in the design.

Requirements
Must have
• Dorian Vitality
• Name: Tomás Lirandel
• Wellness Coach, Consultant & Trainer.
• Website: www.dorianvitality-example.com
• Phone:
• Spain (+34) 612 480 317
• (USA) +1 (555) 610 4829
Nice to have
• The most important is the design of "Dorian Vitality", as this is going to be my personal brand logo. It should be professional, wellness, high end and actual.
Should not have
• no golds, no baroque style..

```html
<!DOCTYPE html>
<html lang="en">
<head>
<meta charset="utf-8">
<title>Tomás Lirandel — Business Card</title>
<link rel="stylesheet" href="https://fonts.googleapis.com/css2?family=Josefin+Sans:wght@300;400&display=swap">
<style>
  :root {
    --card-bg: #ffffff;
    --frame: #4a4a4a;
    --mint: #4ef5b0;
    --mint-soft: #d3fbeb;
    --ink: #3a3a3a;
  }
  html, body {
    margin: 0;
    padding: 0;
    overflow: hidden;
    background: var(--card-bg);
  }
  .card {
    position: relative;
    width: 1200px;
    height: 686px;
    background: var(--card-bg);
    font-family: "Josefin Sans", sans-serif;
    overflow: hidden;
  }
  .card-art {
    position: absolute;
    inset: 0;
  }
  .centered {
    position: absolute;
    transform: translate(-50%, -50%);
    white-space: nowrap;
    text-align: center;
    line-height: 1;
    margin: 0;
  }
  .owner-name {
    left: 600px;
    top: 160px;
    font-size: 104px;
    font-weight: 300;
    letter-spacing: 7px;
    color: var(--mint);
  }
  .role {
    font-size: 46px;
    font-weight: 300;
    letter-spacing: 3px;
    color: var(--ink);
    top: 343px;
  }
  .role--coach { left: 237px; line-height: 1.2; }
  .role--consultant { left: 601px; }
  .role--trainer { left: 967px; }
  .contact {
    position: absolute;
    left: 0;
    width: 1200px;
    top: 462px;
    margin: 0;
    text-align: center;
    color: var(--ink);
    font-weight: 300;
    font-size: 38px;
    letter-spacing: 2px;
    line-height: 47px;
  }
  .contact span { display: block; }
</style>
</head>
<body>
  <main class="card">
    <svg class="card-art" width="1200" height="686" viewBox="0 0 1200 686" aria-hidden="true">
      <rect class="card-frame" x="44" y="44" width="1114" height="598" fill="none" stroke="var(--frame)" stroke-width="2"/>
      <circle class="role-dot" cx="235" cy="341" r="77" fill="var(--mint-soft)"/>
      <circle class="role-dot" cx="601" cy="341" r="77" fill="var(--mint-soft)"/>
      <circle class="role-dot" cx="967" cy="341" r="77" fill="var(--mint-soft)"/>
    </svg>

    <h1 class="centered owner-name">TOMÁS LIRANDEL</h1>

    <p class="centered role role--coach">WELLNESS<br>COACH</p>
    <p class="centered role role--consultant">CONSULTANT</p>
    <p class="centered role role--trainer">TRAINER</p>

    <p class="contact">
      <span class="contact-web">WWW.DORIANVITALITY-EXAMPLE.COM</span>
      <span class="contact-phone">(+34) 612 480 317</span>
      <span class="contact-phone">+1 (555) 610 4829</span>
    </p>
  </main>
</body>
</html>
```